Brightfen Business Card Redesign & Logo Update

We need to update our business cards to something more modern and fresh. Brightfen can provide the current color schemes and old design examples, but welcome creativity in helping us with this redesign. PLEASE NOTE that we no longer utilize the "tree" and/or "leaf" imagery in our branding. If able would apprecaite an update on the quality of our "words only" logo in Ai. / PNG formats too.

Target Market(s)

Investors, landowners, corporate partners, contractors

Industry/Entity Type

Environmental Restoration & Conservation

Contact Information for Business Card

Logo, persons name, title, mailing address, phone and email, website url

Font styles to use
Other font styles liked:
• Merriweather

Requirements
Nice to have
• Logo, persons name, title, mailing address, phone and email, website url, but open to ideams
Should not have
• No all back backgrounds

```html
<!DOCTYPE html>
<html lang="en">
<head>
<meta charset="utf-8">
<title>Brightfen Business Card</title>
<link href="https://fonts.googleapis.com/css2?family=Open+Sans:wght@400;600;700&family=Oswald:wght@500&display=swap" rel="stylesheet">
<style>
  :root {
    --green: #177a3c;
    --orange: #ee7d22;
    --ink: #2b2b2b;
    --muted: #4a4a4a;
    --paper: #ffffff;
    --backdrop: #d9d9d7;
  }
  * { margin: 0; padding: 0; box-sizing: border-box; }
  html, body { width: 1200px; height: 801px; overflow: hidden; }
  body {
    background: var(--backdrop);
    font-family: "Open Sans", Arial, sans-serif;
    position: relative;
  }
  .card {
    position: absolute;
    top: 245px;
    width: 540px;
    height: 310px;
    background: var(--paper);
    border-bottom: 3px solid var(--green);
    box-shadow: 0 10px 30px rgba(0,0,0,0.18);
  }
  .card--info { left: 40px; }
  .card--brand { left: 620px; }

  .wordmark {
    font-family: "Open Sans", Arial, sans-serif;
    font-weight: 700;
    color: var(--green);
    letter-spacing: 1px;
    text-transform: uppercase;
    line-height: 1;
  }
  .tagline {
    font-family: "Oswald", "Arial Narrow", sans-serif;
    font-weight: 500;
    color: var(--ink);
    text-transform: uppercase;
    line-height: 1;
  }

  .card--info .logo { position: absolute; top: 34px; right: 36px; text-align: right; }
  .card--info .wordmark { font-size: 34px; }
  .card--info .tagline { font-size: 13px; margin-top: 5px; letter-spacing: 0.3px; }

  .rule { position: absolute; left: 30px; right: 30px; top: 128px; height: 1px; background: var(--green); }

  .address {
    position: absolute; top: 146px; right: 36px;
    text-align: right; font-size: 13px; line-height: 1.55; color: var(--muted);
  }

  .person { position: absolute; left: 36px; top: 160px; width: 230px; }
  .person__name { font-size: 17px; font-weight: 700; color: var(--green); letter-spacing: 0.5px; text-transform: uppercase; }
  .person__title { font-size: 14px; color: var(--muted); margin-top: 2px; }
  .person__rule { height: 1px; background: var(--green); margin: 12px 0 10px; }

  .contacts { list-style: none; font-size: 13px; color: var(--muted); }
  .contacts li { display: flex; align-items: center; gap: 8px; line-height: 1.6; }
  .contacts svg { width: 11px; height: 11px; flex: none; }

  .card--brand .logo { position: absolute; left: 0; right: 0; top: 112px; text-align: center; }
  .card--brand .wordmark { font-size: 60px; }
  .card--brand .tagline { font-size: 24px; margin-top: 8px; letter-spacing: 0.5px; }
</style>
</head>
<body>

<section class="card card--info">
  <div class="logo">
    <div class="wordmark">Brightfen</div>
    <div class="tagline">Environmental Credit Company</div>
  </div>

  <div class="rule"></div>

  <address class="address" style="font-style:normal">
    1820 Harbor Reach Way<br>
    Port Alder CA 90210
  </address>

  <div class="person">
    <div class="person__name">Dana Kerlow</div>
    <div class="person__title">President</div>
    <div class="person__rule"></div>
    <ul class="contacts">
      <li>
        <svg viewBox="0 0 12 12" aria-hidden="true"><path fill="var(--orange)" d="M2.5 1l2 2.2-1 1.3c.7 1.5 1.8 2.6 3.3 3.3l1.3-1 2.2 2-1 1.6C5.5 10.5 1.5 6.5 1 2z"/></svg>
        555-310-4827
      </li>
      <li>
        <svg viewBox="0 0 12 12" aria-hidden="true"><rect x="1" y="2.5" width="10" height="7" fill="var(--orange)"/><path d="M1 2.5l5 4 5-4" fill="none" stroke="#fff" stroke-width="1"/></svg>
        dkerlow@brightfen.com
      </li>
      <li>
        <svg viewBox="0 0 12 12" aria-hidden="true"><circle cx="6" cy="6" r="5" fill="var(--orange)"/><path d="M1 6h10M6 1c-2 2.5-2 7.5 0 10M6 1c2 2.5 2 7.5 0 10" fill="none" stroke="#fff" stroke-width="0.8"/></svg>
        www.brightfen.com
      </li>
    </ul>
  </div>
</section>

<section class="card card--brand">
  <div class="logo">
    <div class="wordmark">Brightfen</div>
    <div class="tagline">Environmental Credit Company</div>
  </div>
</section>

</body>
</html>
```